Business Card Design Competition

We need a business card design for our Internet Marketing company. We require both front and back designs and the final card must be 89x53mm in size, plus crop marks to 91x55mm. Colours as per logo, plus perhaps black and/or grey (#828282).
Final text must be editable (if you can supply an editable Fireworks PNG, even better)...
FRONT TEXT:
Full Name
Position
Address Line
Suburb, State, Postcode
Phone: 0000 000 000
Mobile: 0000 000 000
Email: xxx@brightlanemedia.com.au
Web: www.brightlanemedia.com.au
Rear of card should be a fresh design plus our slogan text: "Putting You Forward" in large font, then in small text "Kestrel Holdings Pty Ltd (ABN: 42 561 903 774)".
Target Market(s)
Small/Medium Businesses
Industry/Entity Type
Business

```html
<!DOCTYPE html>
<html lang="en">
<head>
<meta charset="utf-8">
<title>Brightlane Media – Business Card</title>
<link rel="stylesheet" href="https://fonts.googleapis.com/css2?family=Jura:wght@400;500&family=Open+Sans:wght@400;700&display=swap">
<style>
  :root {
    --page-bg: #ebe6df;
    --card-edge: #ffffff;
    --card-face: #2a2929;
    --brand-orange: #f39a1e;
    --brand-green: #8cc63f;
    --text-light: #d8d8d8;
    --text-grey: #828282;
  }
  * { margin: 0; padding: 0; box-sizing: border-box; }
  html, body { width: 1200px; height: 900px; overflow: hidden; }
  body { background: var(--page-bg); position: relative; font-family: "Open Sans", sans-serif; }

  .card {
    position: absolute;
    top: 290px;
    width: 548px;
    height: 310px;
    background: var(--card-edge);
    border-radius: 18px;
    padding: 10px;
    box-shadow: 0 3px 10px rgba(0,0,0,0.18);
  }
  .card--front { left: 37px; }
  .card--back { left: 621px; }

  .card__face {
    position: relative;
    width: 100%;
    height: 100%;
    background: var(--card-face);
    border-radius: 10px;
    overflow: hidden;
  }

  .brand-name {
    font-family: "Jura", sans-serif;
    font-weight: 500;
    color: var(--brand-orange);
    line-height: 1;
  }

  /* Front */
  .front__brand { position: absolute; left: 34px; top: 34px; font-size: 44px; }
  .front__brand span { display: block; }
  .front__brand .brand-line-2 { font-size: 32px; margin-top: 2px; }

  .person { position: absolute; left: 34px; top: 150px; }
  .person__name { color: var(--brand-green); font-weight: 700; font-size: 17px; line-height: 1.1; }
  .person__role { color: var(--text-light); font-size: 12px; line-height: 1.2; }

  .address { position: absolute; left: 34px; top: 215px; color: var(--text-light); font-size: 11.5px; }

  .contacts { position: absolute; left: 34px; top: 240px; display: grid; grid-template-columns: 138px auto; row-gap: 3px; }
  .contact { display: flex; align-items: center; gap: 8px; color: var(--text-light); font-size: 11.5px; line-height: 14px; }
  .contact svg { width: 11px; height: 11px; flex: none; }

  .front__mark {
    position: absolute;
    left: 390px;
    top: 140px;
    width: 168px;
    height: 168px;
    border-radius: 50%;
    background: var(--brand-green);
    border: 8px solid var(--card-edge);
  }

  /* Back */
  .back__brand { position: absolute; left: 120px; top: 88px; display: flex; align-items: center; gap: 12px; }
  .back__mark { width: 74px; height: 74px; border-radius: 50%; background: var(--brand-green); flex: none; }
  .back__brand .brand-name { font-size: 34px; }
  .back__brand .brand-name span { display: block; }

  .slogan {
    position: absolute; left: 0; right: 0; top: 196px;
    text-align: center;
    font-family: "Jura", sans-serif;
    font-size: 27px;
    letter-spacing: 3px;
    color: #a3a3a3;
  }
  .legal {
    position: absolute; left: 0; right: 0; top: 258px;
    text-align: center;
    font-size: 11px;
    color: var(--text-grey);
  }
</style>
</head>
<body>

  <section class="card card--front" aria-label="Card front">
    <div class="card__face">
      <div class="brand-name front__brand"><span>Brightlane</span><span class="brand-line-2">Media</span></div>

      <div class="person">
        <p class="person__name">Liam Carver</p>
        <p class="person__role">Company Director</p>
      </div>

      <p class="address">18 harbour view road, Eastfield County Rowe BT19 4KL 5678</p>

      <div class="contacts">
        <p class="contact">
          <svg viewBox="0 0 12 12" aria-hidden="true"><rect x="3" y="0.5" width="6" height="11" rx="1.2" fill="var(--brand-green)"/><rect x="4.2" y="2" width="3.6" height="6" fill="var(--card-face)"/></svg>
          061-555-0142
        </p>
        <p class="contact">
          <svg viewBox="0 0 12 12" aria-hidden="true"><rect x="0.5" y="2.5" width="11" height="7" rx="1" fill="var(--brand-green)"/><path d="M1 3 L6 7 L11 3" stroke="var(--card-face)" stroke-width="1.2" fill="none"/></svg>
          liam@brightlanemedia.com.au
        </p>
        <p class="contact">
          <svg viewBox="0 0 12 12" aria-hidden="true"><path d="M1 4 Q6 0 11 4 L9.5 6 L8 5 L8 3.8 Q6 3 4 3.8 L4 5 L2.5 6 Z" fill="var(--brand-green)"/><rect x="2.5" y="6.5" width="7" height="4.5" rx="1" fill="var(--brand-green)"/></svg>
          061-555-0187
        </p>
        <p class="contact">
          <svg viewBox="0 0 12 12" aria-hidden="true"><circle cx="6" cy="6" r="5" fill="none" stroke="var(--brand-green)" stroke-width="1.4"/><circle cx="6" cy="6" r="2" fill="var(--brand-green)"/></svg>
          brightlanemedia.com.au
        </p>
      </div>

      <div class="front__mark" aria-hidden="true"></div>
    </div>
  </section>

  <section class="card card--back" aria-label="Card back">
    <div class="card__face">
      <div class="back__brand">
        <div class="back__mark" aria-hidden="true"></div>
        <p class="brand-name"><span>Brightlane</span><span>Media</span></p>
      </div>
      <p class="slogan">Putting You Forward</p>
      <p class="legal">Kestrel Holdings Pty Ltd (ABN: 42 561 903 774)</p>
    </div>
  </section>

</body>
</html>
```